A design led business card for the construction industry

High-end business card to match logo. White logo on dark grey/off black to the front. Matching dark font on white to back, possibly with logo design again.

We offer construction and project management services to commercial and private clients in the UK. Projetcs range from newbuilds, conversion of listed buildings and refurbishments and extensions of existing homes. Our focus is on quality and attention to detail using the highest skills.

Contact Information for Business Card

Name; Dorian Keble BSc
Position; Project Manager
Mobile; 07962 408 175
Tel; 01632 960457
email; dorian@stonevale.co.uk
web; www.stonevale.co.uk
Address; Wendle on Thames, KX4 7PW

Colors

Designer to choose only greyscale colors for use in the design.

Requirements
Must have
• To include the below description of the business,

CONSTRUCTION - PROJECT MANAGEMENT
Nice to have
• The posibility of the top back of the card being used as a ruler. So will have a measurement to scale in mm or an architect scale of 1:50
Should not have
• Should not be portrait

```html
<!DOCTYPE html>
<html lang="en">
<head>
<meta charset="utf-8">
<title>Stonevale – Business Card</title>
<link rel="stylesheet" href="https://fonts.googleapis.com/css2?family=Arimo:wght@400;700&display=swap">
<style>
  :root {
    --canvas: #e4e4e4;
    --ink: #0b0b0b;
    --paper: #ffffff;
    --mid-grey: #8c8c8c;
    --soft-grey: #c9c9c9;
    --text-dark: #111111;
  }
  * { box-sizing: border-box; margin: 0; padding: 0; }
  html, body { width: 1200px; height: 900px; overflow: hidden; }
  body {
    background: var(--canvas);
    font-family: "Arimo", Arial, sans-serif;
    position: relative;
  }
  .card {
    position: absolute;
    left: 260px;
    width: 680px;
    height: 388px;
    overflow: hidden;
    box-shadow: 0 6px 18px rgba(0,0,0,0.18);
  }
  .card--front { top: 40px; background: var(--ink); color: var(--paper); }
  .card--back { top: 472px; background: var(--paper); color: var(--text-dark); }

  /* Front */
  .front-brand {
    position: absolute;
    left: 0; right: 0; top: 120px;
    display: flex; flex-direction: column; align-items: center;
  }
  .brand-row { display: flex; align-items: center; gap: 22px; }
  .brand-square {
    width: 34px; height: 34px;
    border: 4px solid currentColor;
  }
  .brand-name {
    font-size: 40px; font-weight: 400;
    letter-spacing: 0.42em;
    margin-right: -0.42em;
  }
  .front-tagline {
    margin-top: 34px;
    font-size: 17px;
    letter-spacing: 0.02em;
  }

  /* Back */
  .person { position: absolute; left: 56px; top: 58px; }
  .person-name { font-size: 25px; font-weight: 700; letter-spacing: 0.01em; }
  .person-name .degree { font-weight: 400; }
  .person-role { font-size: 18px; margin-top: 2px; }

  .back-brand {
    position: absolute; right: 44px; top: 92px;
    display: flex; flex-direction: column; align-items: center; gap: 14px;
    color: var(--text-dark);
  }
  .back-brand .brand-square { width: 30px; height: 30px; border-width: 3px; }
  .back-brand .brand-name { font-size: 24px; letter-spacing: 0.4em; margin-right: -0.4em; }

  .wave { position: absolute; left: 0; top: 0; }

  .contacts {
    position: absolute; left: 56px; top: 184px;
    list-style: none;
    font-size: 19px; line-height: 25px;
  }
  .contacts li { display: flex; align-items: center; gap: 10px; }
  .contacts svg { width: 17px; height: 17px; flex: none; }

  .address {
    position: absolute; right: 44px; bottom: 34px;
    font-size: 17px;
    color: var(--soft-grey);
  }
</style>
</head>
<body>

<section class="card card--front" aria-label="Card front">
  <div class="front-brand">
    <div class="brand-row">
      <span class="brand-square"></span>
      <span class="brand-name">STONEVALE</span>
    </div>
    <p class="front-tagline">CONSTRUCTION - PROJECT MANAGEMENT</p>
  </div>
</section>

<section class="card card--back" aria-label="Card back">
  <svg class="wave" width="680" height="388" viewBox="0 0 680 388" aria-hidden="true">
    <path d="M0,320 C160,328 300,302 434,246 C312,314 170,348 0,345 Z" fill="var(--mid-grey)"/>
    <path d="M0,354 C200,364 330,322 440,260 C540,202 610,174 680,166 L680,388 L0,388 Z"
          fill="var(--ink)" stroke="var(--paper)" stroke-width="4"/>
  </svg>

  <div class="person">
    <p class="person-name">DORIAN KEBLE <span class="degree">BSc</span></p>
    <p class="person-role">Project Manager</p>
  </div>

  <div class="back-brand">
    <span class="brand-square"></span>
    <span class="brand-name">STONEVALE</span>
  </div>

  <ul class="contacts">
    <li>
      <svg viewBox="0 0 16 16"><rect x="3.5" y="1" width="9" height="14" rx="1.5" fill="none" stroke="currentColor" stroke-width="1.6"/><circle cx="8" cy="12.5" r="0.9" fill="currentColor"/></svg>
      <span>07962 408 175</span>
    </li>
    <li>
      <svg viewBox="0 0 16 16"><path d="M4 1.5l2.5 3-1.5 1.8c.8 1.8 2 3 3.8 3.8L10.6 8.6l3 2.5-1.6 2.8C7 13.5 2.4 9 2 3.2z" fill="currentColor"/></svg>
      <span>01632 960457</span>
    </li>
    <li>
      <svg viewBox="0 0 16 16"><rect x="1" y="3.5" width="14" height="9" fill="currentColor"/><path d="M1.5 4l6.5 5 6.5-5" fill="none" stroke="var(--paper)" stroke-width="1.2"/></svg>
      <span>dorian@stonevale.co.uk</span>
    </li>
    <li>
      <svg viewBox="0 0 16 16" fill="none" stroke="currentColor" stroke-width="1.3"><circle cx="8" cy="8" r="6.5"/><ellipse cx="8" cy="8" rx="3" ry="6.5"/><path d="M1.5 8h13M2.5 4.5h11M2.5 11.5h11"/></svg>
      <span>www.stonevale.co.uk</span>
    </li>
  </ul>

  <p class="address">Wendle on Thames, KX4 7PW</p>
</section>

</body>
</html>
```